Local fast-growing company in the service sector

We are looking for a modern business card design, which should also appear on our letterheads

Target Market(s)

Private and industrial sectors

Contact Information for Business Card

Vorname Name
Kellberger Str. 18
73614 Schorndorf
Tel.: 07146-839214-0
Name@agentur-kvtl.de

Colors
9d9d9d
919191
aaaaaa

Requirements
Must have
• The logo (file) in silver

```html
<!DOCTYPE html>
<html lang="de">
<head>
<meta charset="utf-8">
<title>KVTL Visitenkarte</title>
<link href="https://fonts.googleapis.com/css2?family=Open+Sans:wght@400;600;700&display=swap" rel="stylesheet">
<style>
  :root {
    --stage: #2b2b2b;
    --card-dark: #1c1c1c;
    --card-light: #ffffff;
    --silver: #aaaaaa;
    --silver-mid: #9d9d9d;
    --silver-deep: #919191;
    --ink-light: #ffffff;
  }
  * { margin: 0; padding: 0; box-sizing: border-box; }
  html, body {
    width: 1200px; height: 900px; overflow: hidden;
    background: var(--stage);
    font-family: "Open Sans", Arial, sans-serif;
  }
  .card {
    position: absolute;
    left: 320px;
    width: 560px; height: 320px;
    overflow: hidden;
    box-shadow: 0 12px 30px rgba(0,0,0,.45);
  }
  .card--front { top: 110px; background: var(--card-dark); }
  .card--back { top: 470px; background: var(--card-light); }

  .brand {
    position: absolute;
    display: flex; align-items: center; gap: 14px;
  }
  .brand__mark {
    width: 34px; height: 34px;
    background: var(--silver);
  }
  .brand__name {
    font-weight: 700;
    font-size: 56px;
    line-height: 1;
    letter-spacing: 2px;
    color: var(--silver);
  }
  .card--front .brand { left: 150px; top: 108px; }
  .card--back .brand { left: 58px; top: 128px; }
  .brand--back .brand__name { color: var(--silver-deep); }
  .brand--back .brand__mark { background: var(--silver-deep); }

  .front__url {
    position: absolute;
    left: 0; right: 0; top: 226px;
    text-align: center;
    color: var(--ink-light);
    font-size: 13px;
    letter-spacing: 7px;
  }

  .back__panel {
    position: absolute;
    top: 0; right: 0; bottom: 0;
    width: 250px;
    background: linear-gradient(160deg, #b4b4b4 0%, #9d9d9d 100%);
  }

  .contact {
    position: absolute;
    right: 22px; top: 88px;
    text-align: right;
    color: var(--ink-light);
    font-size: 14px;
    line-height: 21px;
  }
  .contact__name { font-weight: 700; letter-spacing: .5px; margin-bottom: 2px; }
  .contact__row { display: flex; justify-content: flex-end; align-items: center; gap: 8px; }
  .contact__icon { width: 12px; height: 12px; flex: none; }
</style>
</head>
<body>

<section class="card card--front" aria-label="Vorderseite">
  <div class="brand">
    <span class="brand__mark"></span>
    <span class="brand__name">KVTL</span>
  </div>
  <p class="front__url">www.agentur-kvtl.de</p>
</section>

<section class="card card--back" aria-label="Rückseite">
  <div class="back__panel" role="img" aria-label="Dekorative silberne Fläche mit aufsteigendem Pfeilschwung"></div>

  <div class="brand brand--back">
    <span class="brand__mark"></span>
    <span class="brand__name">KVTL</span>
  </div>

  <div class="contact">
    <p class="contact__name">VORNAME NAME</p>
    <p>Kellberger Str. 18</p>
    <p>73614 Schorndorf</p>
    <p class="contact__row">07146-839214-0
      <svg class="contact__icon" viewBox="0 0 12 12" aria-hidden="true"><path d="M2 3 C2 1.5 4 1 4.5 2.5 L5 4 L4 5 C4.6 6.4 5.6 7.4 7 8 L8 7 L9.5 7.5 C11 8 10.5 10 9 10 C5 10 2 7 2 3Z" fill="#fff"/></svg>
    </p>
    <p class="contact__row">Name@agentur-kvtl.de
      <svg class="contact__icon" viewBox="0 0 12 12" aria-hidden="true"><rect x="1" y="2.5" width="10" height="7" fill="#fff"/><path d="M1 2.5 L6 6.5 L11 2.5" fill="none" stroke="#9d9d9d" stroke-width="1"/></svg>
    </p>
    <p class="contact__row">www.agentur-kvtl.de
      <svg class="contact__icon" viewBox="0 0 12 12" aria-hidden="true"><circle cx="6" cy="6" r="5" fill="#fff"/><path d="M1 6 H11 M6 1 C4 3.5 4 8.5 6 11 M6 1 C8 3.5 8 8.5 6 11" fill="none" stroke="#9d9d9d" stroke-width=".8"/></svg>
    </p>
  </div>
</section>

</body>
</html>
```